Animal Eye Clinic needs a Business card

We are a new veterinary ophthalmology practice (Ridgeline Pet Vision Care) and we need a business card designed. We only see animal eyes - we are not a regular veterinary clinic. We already have a logo. We are looking for a professional, good looking business card to hand out to our clients. We are looking for something simple but professional and contemporary. Our logo is likely the only picture/graphic that needs to be on the card.
Updates

Contact Information for Business Card

Delia Vossman, BSc, DVM, MSc, DipACVO
Veterinary Ophthalmologist

Phone: 250.418.3927
Email: ridgelinepetvisioncare@mailbox-example.net
Website: ridgelinepetvisioncare-example.net
Address: 1874 Thornbury Rd
Kelowna, BC, V1X 4M9

Colors

Designer to choose colors to be used in the design.

Requirements
Must have
• Our logo (attached)

```html
<!DOCTYPE html>
<html lang="en">
<head>
<meta charset="utf-8">
<title>Ridgeline Pet Vision Care – Business Card</title>
<link href="https://fonts.googleapis.com/css2?family=Montserrat:wght@300;400;500;600;700&display=swap" rel="stylesheet">
<style>
  :root {
    --teal: #0e8fa3;
    --ink: #4a4a4a;
    --grey-mid: #7a7a7a;
    --card-white: #ffffff;
    --card-grey: #676767;
    --card-grey-deep: #585858;
    --card-grey-light: #ececec;
    --backdrop: #e4e6e8;
  }
  * { box-sizing: border-box; margin: 0; padding: 0; }
  html, body {
    width: 1200px; height: 1125px; overflow: hidden;
    background: var(--backdrop);
    font-family: "Montserrat", Arial, sans-serif;
  }
  .canvas { position: relative; width: 1200px; height: 1125px; }
  .card {
    position: absolute; left: 150px; width: 900px; height: 514px;
    overflow: hidden; border-bottom: 5px solid var(--teal);
    box-shadow: 0 10px 26px rgba(0,0,0,.18);
  }
  /* Front */
  .card--front { top: 30px; background: var(--card-white); }
  .brand {
    position: absolute; left: 48px; top: 44px;
    display: flex; align-items: center; gap: 14px;
  }
  .brand__dot { width: 52px; height: 52px; border-radius: 50%; background: var(--teal); }
  .brand__name { color: var(--teal); font-weight: 600; line-height: 1.05; text-transform: uppercase; }
  .brand__line1 { display: block; font-size: 18px; letter-spacing: 9px; }
  .brand__line2 { display: block; font-size: 24px; letter-spacing: .5px; }
  .person { position: absolute; left: 60px; top: 136px; }
  .person__marker {
    position: absolute; left: -60px; top: 6px; width: 0; height: 0;
    border-top: 12px solid transparent; border-bottom: 12px solid transparent;
    border-left: 20px solid var(--teal);
  }
  .person__name { color: var(--teal); font-weight: 700; font-size: 28px; letter-spacing: 2.5px; text-transform: uppercase; }
  .person__creds { color: var(--teal); font-size: 18px; font-weight: 400; margin-top: 6px; }
  .person__title { color: var(--ink); font-size: 19px; font-weight: 400; margin-top: 4px; }
  .address {
    position: absolute; left: 60px; top: 262px;
    color: var(--ink); font-size: 19px; font-weight: 300; font-style: normal; line-height: 1.45;
  }
  .contacts {
    position: absolute; left: 50px; top: 350px; list-style: none;
    color: var(--ink); font-size: 17px; font-weight: 400; line-height: 1.6;
  }
  .contacts li { display: flex; align-items: center; gap: 6px; white-space: nowrap; }
  .contacts svg { width: 16px; height: 16px; fill: var(--teal); flex: none; }
  .front-art { position: absolute; right: 0; top: 0; width: 400px; height: 514px; }
  /* Back */
  .card--back { top: 581px; background: var(--card-grey); }
  .back-art { position: absolute; left: 0; top: 0; width: 520px; height: 514px; }
  .back-brand {
    position: absolute; right: 60px; top: 210px; text-align: right;
    text-transform: uppercase; line-height: 1.1;
  }
  .back-brand__line1 {
    display: block; font-size: 22px; letter-spacing: 14px; margin-right: -14px;
    color: var(--card-grey-light); font-weight: 400;
  }
  .back-brand__line2 { display: block; font-size: 34px; letter-spacing: .5px; color: var(--teal); font-weight: 600; }
</style>
</head>
<body>
<main class="canvas">

  <section class="card card--front" aria-label="Business card front">
    <div class="brand">
      <span class="brand__dot"></span>
      <span class="brand__name">
        <span class="brand__line1">Ridgeline</span>
        <span class="brand__line2">Pet Vision Care</span>
      </span>
    </div>

    <div class="person">
      <span class="person__marker"></span>
      <h1 class="person__name">Delia Vossman</h1>
      <p class="person__creds">BSc, DVM, MSc, DipACVO</p>
      <p class="person__title">Veterinary Ophthalmologist</p>
    </div>

    <address class="address">1874 Thornbury Rd<br>Kelowna, BC, V1X 4M9</address>

    <ul class="contacts">
      <li><svg viewBox="0 0 16 16"><path d="M3.6 1.2l2.3 2.6-1.2 1.9c.9 2 2.5 3.6 4.5 4.6l1.9-1.2 2.6 2.3-1.3 2.4C7.6 13.4 2.6 8.4 1.2 3.6z"/></svg>250.418.3927</li>
      <li><svg viewBox="0 0 16 16"><path d="M1 3h14v10H1z M1.6 3.6L8 8.6l6.4-5" stroke="#fff" stroke-width="1.2"/></svg>ridgelinepetvisioncare@mailbox-example.net</li>
      <li><svg viewBox="0 0 16 16"><circle cx="8" cy="8" r="7"/><path d="M1 8h14M8 1c-3 3.5-3 10.5 0 14M8 1c3 3.5 3 10.5 0 14" stroke="#fff" stroke-width="1" fill="none"/></svg>ridgelinepetvisioncare-example.net</li>
    </ul>

    <svg class="front-art" viewBox="0 0 400 514" role="img" aria-label="Large illustration of a horse, dog and cat in teal and grey">
      <defs>
        <linearGradient id="frontArtTone" x1="0" y1="0" x2="0" y2="1">
          <stop offset="0" stop-color="#0e8fa3"/>
          <stop offset="0.7" stop-color="#0e8fa3"/>
          <stop offset="1" stop-color="#7a7a7a"/>
        </linearGradient>
      </defs>
      <ellipse cx="280" cy="300" rx="220" ry="270" fill="url(#frontArtTone)"/>
    </svg>
  </section>

  <section class="card card--back" aria-label="Business card back">
    <svg class="back-art" viewBox="0 0 520 514" role="img" aria-label="Blind-embossed illustration of a horse, dog and cat">
      <ellipse cx="230" cy="300" rx="210" ry="250" fill="var(--card-grey-deep)"/>
    </svg>
    <div class="back-brand">
      <span class="back-brand__line1">Ridgeline</span>
      <span class="back-brand__line2">Pet Vision Care</span>
    </div>
  </section>

</main>
</body>
</html>
```